Technical Communications firm needs an article turned into a white paper

We want to redesign a 3-part blog series into a white paper that we can print for a conference. I've consolidated the three posts into the attached Word document.

We are looking for a light, easy to read design. Good use of graphics to support the message. I've added the graphics we used in the original post.

You can view them at
http://www.brightquillpages.com/blog/are-you-satisfied-with-your-dita-solution/

Target Market(s)

Product managers from High-tech, Finance, and Medical industries.

Industry/Entity Type

Information Technology

Colors

Designer to choose colors to be used in the design.

Requirements
Must have
• Must be modern, light, easy to read and slick design. Try to incorporate the graphics provided, but feel free to add more. Must retain the lists and tables.
• Must align with our website/brand.
• Must be easy to read. So not too busy.
• Please move all footnotes to endnotes. You'll need to rework the numbering.
Nice to have
• Awesome coverpage.
Should not have
• Hokey clipart. Not too heavy or hard to read.

```html
<!DOCTYPE html>
<html lang="en">
<head>
<meta charset="utf-8">
<title>Brightquill Pages White Paper – Pages 3 and 4</title>
<link href="https://fonts.googleapis.com/css2?family=Exo+2:wght@600;700;800&family=Hind:wght@400;500;600&display=swap" rel="stylesheet">
<style>
:root{
  --navy:#1f2a86;
  --blue:#29a8df;
  --ink:#3a3a3a;
  --rule:#c9ccd3;
  --note:#e5e6ea;
  --page:#ffffff;
  --backdrop:#e8e8eb;
}
*{box-sizing:border-box;margin:0;padding:0}
html,body{width:1200px;height:1200px;overflow:hidden;background:var(--backdrop)}
body{position:relative;font-family:"Hind",Arial,sans-serif;color:var(--ink)}
.page{position:absolute;top:243px;width:505px;height:714px;background:var(--page);overflow:hidden}
.page--three{left:68px}
.page--four{left:627px}
.block{position:absolute;left:30px;width:444px}
.body-text{font-size:7.5px;line-height:9.2px;text-align:justify}
.heading{font-family:"Exo 2",sans-serif;font-weight:700;color:var(--navy);font-size:12px}
.spec-table{top:103px;height:175px;border:1px solid var(--rule);border-radius:8px;overflow:hidden;display:grid;grid-template-columns:1fr 1fr;grid-template-rows:20px repeat(4,1fr)}
.spec-table .th{background:var(--blue);color:#fff;font-size:8px;display:flex;align-items:center;justify-content:center;font-weight:500}
.spec-table .th:first-child{border-right:1px solid #fff}
.spec-table .td{font-size:7.4px;line-height:9px;padding:6px 9px;border-top:1px solid var(--rule);text-align:justify;display:flex;align-items:center}
.spec-table .td:nth-child(odd){border-right:1px solid var(--rule)}
.caption{font-size:7.2px}
.caption a,.ref{color:var(--blue)}
.section-head{position:absolute;left:30px;height:32px;display:flex;align-items:center}
.section-icon{width:32px;height:32px;border-radius:50%;border:2px solid var(--navy);background:#fff;position:relative;z-index:2;display:flex;align-items:center;justify-content:center}
.section-pill{margin-left:-2px;height:15px;background:var(--blue);color:#fff;border-radius:0 8px 8px 0;padding:0 10px 0 6px;font-family:"Exo 2",sans-serif;font-weight:700;font-size:8.8px;display:flex;align-items:center;letter-spacing:.2px;white-space:nowrap}
.bullets{list-style:none}
.bullets li{position:relative;padding-left:16px;font-size:7.5px;line-height:9.2px;text-align:justify}
.bullets li::before{content:"";position:absolute;left:0;top:1px;width:8px;height:8px;border-radius:50%;border:1.6px solid var(--blue);box-sizing:border-box}
.bullets li::after{content:"";position:absolute;left:2.6px;top:3.4px;width:3px;height:3px;background:var(--navy);border-radius:50%}
.endnotes{position:absolute;left:0;top:589px;width:505px;height:92px;background:var(--note);padding:9px 30px}
.endnotes p{font-size:7.2px;line-height:9px;font-style:italic;position:relative;padding-left:16px;margin-bottom:5px;text-align:justify}
.endnotes b{position:absolute;left:0;color:var(--blue);font-weight:400}
.footer-band{position:absolute;left:0;top:683px;width:505px;height:18px;background:var(--blue);color:#fff;font-size:7.8px;letter-spacing:3.4px;display:flex;align-items:center;justify-content:center}
.footer-rule{position:absolute;left:0;top:703px;width:505px;height:3px;background:var(--navy)}
.page-num{position:absolute;left:456px;top:678px;width:28px;height:28px;border-radius:50%;background:#fff;border:2px solid var(--navy);font-size:9px;display:flex;align-items:center;justify-content:center;color:var(--navy);font-weight:500}
.part-title{position:absolute;top:26px;width:505px;text-align:center;font-family:"Exo 2",sans-serif;font-weight:800;font-size:25px;color:var(--navy)}
.part-title span{color:var(--blue)}
.title-rule{position:absolute;top:66px;left:0;width:505px;height:3px;background:linear-gradient(90deg,var(--navy) 0 73%,var(--blue) 73% 100%)}
.hero{position:absolute;top:70px;left:0;width:505px;height:228px;background:linear-gradient(180deg,#c9cbcf 0%,#e8e9ea 45%,#d3d4d6 75%,#b9babd 100%)}
.hero-rule{position:absolute;top:299px;left:0;width:505px;height:3px;background:linear-gradient(90deg,var(--navy) 0 40%,var(--blue) 40% 100%)}
</style>
</head>
<body>

<section class="page page--three">
  <h2 class="heading block" style="top:30px">Selecting the best training for your needs.</h2>
  <p class="block body-text" style="top:52px">There are many training options available to learn about DITA. Selecting the best training for your team entails examining what it is you need to learn. Most DITA training courses cover the features and walk you through the structures and mechanics of the standard. These courses demonstrate how to markup content, but will often not teach you how to rethink and restructure your content to take advantage of DITA's features. Consider the differences between structured writing and structured markup.</p>

  <div class="block spec-table">
    <div class="th">STRUCTURED WRITING</div>
    <div class="th">STRUCTURED MARKUP</div>
    <div class="td">Coined by Robert Hale in the 1960's as a means of analyzing, organizing, and presenting information for optimal human consumption</div>
    <div class="td">Allows authors to markup words, phrases, and sections of content for presentation and for meaning for consumption by machines</div>
    <div class="td">Promotes patterns for format and syntax that become easily recognizable and predictable</div>
    <div class="td">Is validated using standard sets of rules that specify consistent and predictable patterns</div>
    <div class="td">Relies on consistently labelling and chunking information into easily scannable text</div>
    <div class="td">Specifies what content goes where but does not limit or restrict how the content is written</div>
    <div class="td">Introduces universal information typing based on intended reader response</div>
    <div class="td">Provides a rich underlying metadata layer for capturing properties related to the content</div>
  </div>
  <p class="block caption" style="top:290px">Table reproduced from "Powering Team Productivity from the Front of the XML Train<a>[iii]</a>".</p>

  <div class="section-head" style="top:314px">
    <div class="section-icon"><svg width="18" height="18" viewBox="0 0 24 24" fill="none" stroke="#1f2a86" stroke-width="2"><path d="M4 12a8 8 0 0 1 13.7-5.6"/><path d="M20 12a8 8 0 0 1-13.7 5.6"/><path d="M18 2v5h-5"/><path d="M6 22v-5h5"/></svg></div>
    <div class="section-pill" style="width:216px">CONTINUOUS COLLABORATIVE LEARNING</div>
  </div>
  <p class="block body-text" style="top:354px">Organizations that wisely invest in comprehensive training for their writing teams also recognize the importance of continuous learning and recurring training. To stay on top of knowledge sharing in your team, consider the following collaboration activities:</p>
  <ul class="block bullets" style="top:384px">
    <li style="margin-bottom:8px">Schedule regular checkpoints where your team discusses what they've learned with other members of the team.</li>
    <li style="margin-bottom:6px">Assign different members of your team to research and present best practices at regularly scheduled lunch-and-learn sessions.</li>
    <li style="margin-bottom:8px">Attend webinars and seminars on best practices as a group and then debrief together to discuss aspects that should be incorporated into your day-to-day work.</li>
    <li style="margin-bottom:8px">Review and update your content standards regularly as a team to keep your procedures and guidelines current and relevant.</li>
    <li>Pair up senior members of your team with new or junior members for regular mentoring and coaching.</li>
  </ul>

  <div class="section-head" style="top:499px">
    <div class="section-icon"><svg width="18" height="18" viewBox="0 0 24 24" fill="none" stroke="#1f2a86" stroke-width="2"><rect x="9" y="3" width="12" height="9"/><circle cx="5" cy="7" r="2"/><path d="M3 21v-9h4l4-2M7 12v9"/></svg></div>
    <div class="section-pill" style="width:276px">BRIGHTQUILL PAGES® STRUCTURED AUTHOR TRAINING</div>
  </div>
  <p class="block body-text" style="top:537px">Brightquill Pages has many years of experience teaching organizations how to write better structured content. Our inhouse, instructor-led training courses run from 1 to 5 days depending on your needs and cover the gamut of tools and techniques needed for successful structured authoring. Learn more about our DITA training. Or contact Brightquill Pages to find out more about how we can address your specific training needs.</p>

  <div class="endnotes">
    <p><b>[i]</b>Structured Content Pulse Survey published by The Copy Drover on May 31, 2017. Listen to an analysis of the results by Ron Harlow, Kevin Sandoval-Ross, Mark Lindqvist, and Scott Amory and download a copy of the results today from ClearCast at https://www.clearcast.example/webcast/9273/259775</p>
    <p><b>[ii]</b>How Readers Think About Smart Content presented by Ron Harlow on July 21, 2016. See https://www.clearcast.example/webcast/9273/214245 for details.</p>
    <p><b>[iii]</b>Powering Team Productivity from the Front of the XML Train presented by Ron Harlow and Dale Gorton at Content Forum West 2017 in Harbor City.</p>
  </div>
  <div class="footer-band">www.brightquillpages.com</div>
  <div class="footer-rule"></div>
  <div class="page-num">03</div>
</section>

<section class="page page--four">
  <h1 class="part-title">PART 2: <span>TECHNOLOGY</span></h1>
  <div class="title-rule"></div>
  <div class="hero" role="img" aria-label="Photo: a red hot air balloon tethered to a heavy iron anchor, lifting it against a grey cloudy sky"></div>
  <div class="hero-rule"></div>

  <p class="block body-text" style="top:311px">This article is part of a series based on the results of a survey of more than 250 technical communication professionals conducted by The Copy Drover in 2017 entitled The Structured Content Pulse Survey <span class="ref">[i]</span>. In the survey, almost two-thirds of respondents voiced some concerns with their DITA deployment.</p>
  <p class="block body-text" style="top:349px">In my previous article, I examined some of the principal issues related to skills development. This article looks at how technology affects overall DITA satisfaction.</p>

  <div class="section-head" style="top:372px">
    <div class="section-icon"><svg width="18" height="18" viewBox="0 0 24 24" fill="none" stroke="#1f2a86" stroke-width="2"><rect x="7" y="7" width="10" height="10"/><path d="M10 3v4M14 3v4M10 17v4M14 17v4M3 10h4M3 14h4M17 10h4M17 14h4"/></svg></div>
    <div class="section-pill" style="width:214px">ISSUES RELATED TO TECHNOLOGY</div>
  </div>
  <p class="block body-text" style="top:410px">The second highest ranked reported issues fall under the category of technology. These include</p>
  <ul class="block bullets" style="top:427px">
    <li style="margin-bottom:7.5px">Our technology doesn't meet our expectations. Ranked 4th by 62% of respondents</li>
    <li style="margin-bottom:7.5px">Our publishing capabilities are limited. Ranked 5th by 60% of respondents, and</li>
    <li style="margin-bottom:7.5px">We have challenges with content localization. Ranked 10th by 35% of respondents.</li>
    <li>We often hear about the failure of the technology as it relates to performance or complexity. While technology may seem the most likely culprit, it is often not the root cause of the problem.</li>
  </ul>
  <p class="block body-text" style="top:506px">The good news is that you have invested in an open standard and your systems likely make it possible to lift your content—and much of your metadata—out of your existing system and put it into an entirely new system with relatively minor disruption. Or if your entire system isn't the problem, you can often replace components of your solution with components from other vendors to achieve a better result. Lastly, because your content is in XML, it can often be refactored to correct problems that have accumulated in your content over time.</p>
  <p class="block body-text" style="top:562px">Before we look at changing your technology, we should examine some of these problems to see if we can identify a more appropriate root cause.</p>

  <div class="section-head" style="top:584px">
    <div class="section-icon"><svg width="18" height="18" viewBox="0 0 24 24" fill="none" stroke="#1f2a86" stroke-width="2"><circle cx="13" cy="13" r="8"/><path d="M13 9v4l3 2M11 2h4M3 10h3M2 14h3"/></svg></div>
    <div class="section-pill" style="width:174px">PERFORMANCE PROBLEMS</div>
  </div>
  <p class="block body-text" style="top:621px">Common complaints regarding performance include observations that processes take longer or systems are slower to respond than they were before the move to DITA. Part of this observation may be related to aligning to different expectations. You are working with a lot more parts and potentially with many more people to get the job done. Some parts of the process will naturally take longer. These perceived issues will appear worse when you are required to collaborate with writers, editors, and other team members across great distances.</p>

  <div class="footer-band">www.brightquillpages.com</div>
  <div class="footer-rule"></div>
  <div class="page-num">04</div>
</section>

</body>
</html>
```